Website for Reiki and Wellness Courses

I teach online courses in Reiki and wellness/self-development and am needing a new website.

The focus of the website will be to provide descriptions of the courses as well as include a blog and pages where students in my courses will visit for additional information.

Note: courses are NOT hosted on this site.
The focus of this website will be to encourage viewers to enroll in courses as well as opt in to the email list.

I will upload copy soon. My old website is: http://brightfernstudies.example. Please do not use existing logo.

Target Market(s)

Alternative health, wellness, spirituality, personal development. Males and females of all ages seeking to improve their health and life.

Industry/Entity Type

Health And Wellness

Logo Text

No text (please do not use existing logo)

Coding

Coded - Design and coding required

Number of Pages Required

5+ page

Requirements
Must have
• 1. Home page
• 2. About page
• 3. Courses page that outlines courses (there are currently 6 courses with 1 coming soon)
• 4. Individual course page (maybe a template that I can adjust color and pictures for with each course)
• 5. Blog
• 6. Student Area that outlines all Student Areas
• 7. Individual Student Area page (maybe a template that I can adjust color and pictures for with each course)
• 8. Shop page (note: items will not currently be purchased through website - it will be a link to quillmarket for a book).
• 9. Student thank-you page (maybe a template that I can adjust color and pictures for with each course) this is the page students are directed to at end of course with vouchers for other courses.
• Opt-in for the home page, course pages, blog and thank-you pages
Nice to have
• I would like the design to be calm, clean and soothing. Ideally visitors feel relaxed when viewing the site and are encouraged to explore the courses, subscribe to the email list and purchase a product.
• ~ Testimonials page
• ~ Contact page
• I tend to gravitate towards blues, greys and purples as well as monochromatic color schemes.
Should not have
• Contact form on home page
• phone number on home page
• location/physical address
• dates for blog posts

```html
<!DOCTYPE html>
<html lang="en">
<head>
<meta charset="utf-8">
<title>Bright Fern Studies – Reiki &amp; Wellness Courses</title>
<link href="https://fonts.googleapis.com/css2?family=Raleway:wght@400;500;600;700&family=Open+Sans:wght@400;600;700&family=Lora:ital@1&display=swap" rel="stylesheet">
<style>
:root{
  --purple:#9a3f9f;
  --purple-dark:#7d2e84;
  --navy:#2d3f95;
  --blue:#3b4ea2;
  --green:#5cb94a;
  --text:#555a66;
  --muted:#8a8f99;
  --light:#f3f4f6;
  --white:#ffffff;
}
*{box-sizing:border-box;margin:0;padding:0}
html,body{width:1200px;height:3814px;overflow:hidden}
body{position:relative;font-family:"Open Sans",Arial,sans-serif;color:var(--text);background:var(--white)}
section,header,footer{position:absolute;left:0;width:1200px}
.abs{position:absolute}
.ph{position:absolute}

/* header + hero */
.hero{top:0;height:660px;background:linear-gradient(180deg,#d9eef6 0%,#eef7fa 35%,#bfdbe6 62%,#9cc3d2 100%)}
.hero-figure{left:470px;top:190px;width:260px;height:360px;border-radius:130px 130px 20px 20px;background:linear-gradient(180deg,rgba(240,240,240,.0),rgba(235,232,228,.85) 40%,rgba(196,178,150,.9))}
.logo{left:76px;top:20px;height:62px;display:flex;align-items:center;gap:12px;white-space:nowrap}
.logo-dot{width:56px;height:56px;border-radius:50%;background:var(--purple);flex:none}
.logo-name{font-family:"Raleway",sans-serif;font-weight:600;font-size:18px;color:var(--purple-dark);letter-spacing:.3px;border-left:1px solid #c9a7cc;padding-left:12px}
.nav{right:90px;top:34px;display:flex;gap:8px;align-items:center;list-style:none;white-space:nowrap}
.nav li{font-family:"Raleway",sans-serif;font-size:15px;font-weight:500;color:#3b3f52;padding:9px 16px;border-radius:24px}
.nav li.active{background:var(--purple);color:var(--white)}
.hero-title{top:258px;width:1200px;text-align:center;font-family:"Open Sans",sans-serif;font-weight:700;font-size:46px;color:var(--navy)}
.hero-sub{top:326px;left:340px;width:520px;text-align:center;font-family:"Lora",serif;font-style:italic;font-size:17px;color:#2f3142;line-height:1.55}
.btn{display:inline-block;font-family:"Raleway",sans-serif;font-weight:600;text-transform:uppercase;text-align:center;border-radius:30px}
.btn-green{left:502px;top:406px;width:198px;height:54px;line-height:54px;background:var(--green);color:var(--white);font-size:19px}

/* welcome */
.welcome{top:520px;height:510px}
.welcome svg{position:absolute;left:0;top:0}
.welcome-photo{left:820px;top:118px;width:290px;height:382px;background:linear-gradient(160deg,#c9a6cb,#eadfe9 55%,#d9c6da);border-radius:6px}
.welcome-kicker{left:78px;top:146px;font-family:"Raleway",sans-serif;font-size:17px;color:var(--white);letter-spacing:.5px}
.welcome-title{left:78px;top:170px;font-family:"Raleway",sans-serif;font-weight:700;font-size:38px;color:var(--white)}
.welcome-text{left:78px;top:232px;width:720px;font-size:13.5px;line-height:20px;color:#f5e9f6}
.btn-outline{left:78px;top:398px;width:176px;height:56px;line-height:52px;border:2px solid var(--white);color:var(--white);font-size:19px;text-transform:uppercase}

/* courses */
.courses{top:1030px;height:818px;background:linear-gradient(180deg,#f6f6f7,#ececee)}
.section-title{width:1200px;text-align:center;font-family:"Raleway",sans-serif;font-size:40px;font-weight:500;letter-spacing:1px;color:var(--navy)}
.section-title b{font-weight:700;color:var(--purple)}
.courses .section-title{top:52px}
.intro{left:165px;top:110px;width:870px;text-align:center;font-size:14.5px;line-height:23px;color:var(--text)}
.hub{left:470px;top:280px;width:300px;height:330px;border-radius:50%;background:radial-gradient(circle,#e6e0ec 0%,#d9d2e0 55%,rgba(236,236,238,0) 72%)}
.thumb{width:128px;height:128px;border-radius:50%;border:3px solid var(--white);box-shadow:0 2px 6px rgba(0,0,0,.12)}
.course{width:280px;font-size:13.5px;line-height:21px;color:var(--muted)}
.course h3{font-family:"Open Sans",sans-serif;font-size:15px;font-weight:600;color:#3a3d48;margin-bottom:6px;line-height:21px}
.course.left{text-align:right}
.course.left h3{color:#8a8f99;font-weight:400}
.course.center{text-align:center}

/* testimonial */
.testimonial{top:1848px;height:394px;background:linear-gradient(90deg,#3a4ea2,#4257aa 55%,#5266b0)}
.testimonial .section-title{top:48px;color:var(--white);font-weight:400}
.testimonial .section-title b{color:var(--white)}
.quote-badge{left:558px;top:112px;width:84px;height:84px;border:3px solid var(--white);border-radius:22px}
.arrow{width:50px;height:50px;border:2px solid var(--white);border-radius:50%}
.quote{left:140px;top:240px;width:920px;text-align:center;font-size:14.5px;line-height:24px;color:var(--white)}
.author{top:322px;width:1200px;text-align:center;font-size:15px;font-weight:700;color:var(--white)}

/* blog */
.blog{top:2242px;height:559px;background:#f7f7f8}
.blog .section-title{top:70px;font-weight:400}
.card{top:142px;width:242px}
.card-img{width:242px;height:166px}
.card h4{margin-top:34px;font-family:"Raleway",sans-serif;font-weight:500;font-size:16px;line-height:22px;color:#3a3d48}
.card p{margin-top:12px;font-size:13.5px;line-height:21px;color:#6b6f7a}
.card .more{margin-top:10px;font-family:"Raleway",sans-serif;font-weight:700;font-size:14px;color:#2f3142;display:flex;align-items:center;gap:6px}

/* opt-in */
.optin{top:2801px;height:415px;background:linear-gradient(100deg,#f3e6a0 0%,#c9d98a 30%,#6f9b52 62%,#4d7a3e 100%)}
.optin-figure{left:20px;top:90px;width:330px;height:300px;border-radius:40%;background:radial-gradient(circle,rgba(255,250,230,.85),rgba(255,246,210,0) 70%)}
.optin-title{left:656px;top:56px;font-family:"Raleway",sans-serif;font-size:38px;color:var(--white);letter-spacing:1px}
.optin-title b{font-weight:700}
.optin-text{left:496px;top:108px;width:640px;font-size:14px;line-height:21px;color:var(--white)}
.field{width:361px;height:41px;background:var(--white);border:1px solid #d8d8d8;border-radius:4px;padding-left:14px;line-height:39px;font-size:13.5px;color:#8a8f99}
.btn-purple{left:686px;top:313px;width:247px;height:48px;line-height:48px;background:var(--purple);color:var(--white);font-size:18px;text-transform:uppercase}

/* newsletter + footer */
.newsletter{top:3216px;height:598px;background:linear-gradient(180deg,#f6f6f7 0%,#eeeef0 30%,#b9bcc7 62%,#8e92a3 100%)}
.newsletter .section-title{top:58px;font-weight:400;color:var(--navy)}
.news-text{left:290px;top:122px;width:620px;text-align:center;font-size:14.5px;line-height:24px;color:#4a4e5a}
.news-input{left:275px;top:178px;width:455px;height:51px;background:var(--white);border:1px solid #d6d6da;border-radius:4px;padding-left:18px;line-height:49px;font-size:14px;color:#8a8f99}
.btn-blue{left:740px;top:178px;width:185px;height:51px;line-height:51px;background:var(--blue);color:var(--white);font-size:19px;border-radius:30px}
.social{width:48px;height:48px;border:2px solid var(--white);transform:rotate(45deg)}
.foot-nav{top:492px;width:1200px;display:flex;justify-content:center;gap:14px;list-style:none}
.foot-nav li{font-family:"Raleway",sans-serif;font-size:16px;color:var(--white);padding:8px 22px;border-radius:24px}
.foot-nav li.active{border:2px solid var(--white);background:rgba(255,255,255,.15)}
.copyright{top:540px;width:1200px;text-align:center;font-size:14px;color:var(--white)}
</style>
</head>
<body>

<header class="hero">
  <div class="ph hero-figure" role="img" aria-label="Photo of a person meditating at the end of a wooden pier over calm water"></div>
  <div class="abs logo"><span class="logo-dot"></span><span class="logo-name">BRIGHT FERN STUDIES</span></div>
  <ul class="abs nav">
    <li class="active">HOME</li><li>ABOUT</li><li>COURSES</li><li>BLOG</li><li>STUDENT AREAS</li><li>CONTACT</li>
  </ul>
  <h1 class="abs hero-title">Become a Certified USUI Reiki Master</h1>
  <p class="abs hero-sub">This comprehensive online course gives you all of the tools you need to be certified as a Traditional Usui Reiki Master.</p>
  <span class="abs btn btn-green">Know More</span>
</header>

<section class="welcome">
  <svg width="1200" height="510" viewBox="0 0 1200 510" aria-hidden="true">
    <polygon points="0,0 600,118 1200,0 1200,510 0,510" fill="var(--purple)"/>
  </svg>
  <div class="ph welcome-photo" role="img" aria-label="Photo of a woman seated cross-legged in a meditation pose"></div>
  <p class="abs welcome-kicker">WELCOME TO</p>
  <h2 class="abs welcome-title">BRIGHT FERN STUDIES</h2>
  <div class="abs welcome-text">
    <p>Thought to be centuries old and rediscovered in the late 1800's, Reiki (pronounced ray-key) is a healing and enlightenment system. Reiki can be translated into "Universal (Rei) Life Energy (Ki)". As a practitioner of Reiki, you attune your awareness to this energy and utilize it for the physical and emotional healing of self and others.</p>
    <p>Reiki is non-denominational and can be practiced by everyone, regardless of their religious and spiritual beliefs. Reiki can be performed hands-on in person or from a distance.</p>
  </div>
  <span class="abs btn btn-outline">Know More</span>
</section>

<section class="courses">
  <h2 class="abs section-title">OUR <b>COURSES</b></h2>
  <p class="abs intro">Online learning gives you the opportunity to tailor your course to meet your needs. If you are very interested in a specific topic, you can spend more time on it, research connections and reflect on how it applies to your every day life.</p>
  <div class="ph hub" role="img" aria-label="Photo of a woman in a seated yoga stretch on a mat"></div>

  <div class="ph thumb" style="left:399px;top:197px;background:linear-gradient(135deg,#e9c27a,#c98a4a)" role="img" aria-label="Photo of a woman stretching outdoors"></div>
  <div class="abs course left" style="left:94px;top:200px"><h3>Reiki Level I, II Master<br>Certification</h3><p>Learn about Reiki, a universal energy that has been used successfully all over the...</p></div>

  <div class="ph thumb" style="left:361px;top:363px;background:linear-gradient(135deg,#d9e6f2,#9fb6cc)" role="img" aria-label="Photo of a small white dog"></div>
  <div class="abs course left" style="left:64px;top:356px"><h3 style="color:#3a3d48;font-weight:600">Animal Reiki Practitioner<br>Certification</h3><p>In this course you will learn how to use Animal Reiki, a simple, non-invasive alternative therapy...</p></div>

  <div class="ph thumb" style="left:361px;top:520px;background:linear-gradient(135deg,#d79a64,#a6643a)" role="img" aria-label="Photo of healing crystals being placed on the back"></div>
  <div class="abs course left" style="left:56px;top:532px"><h3 style="color:#3a3d48;font-weight:600">Crystak Reiki Practitioner<br>Certification</h3><p>Become a Certified Reiki Master with an interactive online course...</p></div>

  <div class="ph thumb" style="left:681px;top:197px;background:linear-gradient(135deg,#f0ece6,#cfc4b6)" role="img" aria-label="Photo of a person sitting calmly from behind"></div>
  <div class="abs course" style="left:831px;top:200px"><h3>Acupressure and Reiki for Anxiety and Depression</h3><p>Do you feel down more often than up? Or do you find fear is preventing you from moving...</p></div>

  <div class="ph thumb" style="left:744px;top:350px;background:linear-gradient(135deg,#eef1f4,#c3ccd6)" role="img" aria-label="Photo of a woman meditating on a white background"></div>
  <div class="abs course" style="left:882px;top:372px"><h3>Your Soul is Calling</h3><p>What would it be like to live the life you were meant to live? To have the world around you...</p></div>

  <div class="ph thumb" style="left:729px;top:520px;background:linear-gradient(135deg,#e3a078,#b66b48)" role="img" aria-label="Photo of a relaxing massage"></div>
  <div class="abs course" style="left:882px;top:532px"><h3>Sacred Sound and Breath</h3><p>Become a Certified Reiki Master with an interactive online course...</p></div>

  <div class="ph thumb" style="left:533px;top:576px;background:linear-gradient(135deg,#f2f2f2,#c9ccd2)" role="img" aria-label="Photo of a woman working at a laptop"></div>
  <div class="abs course center" style="left:460px;top:720px"><h3 style="margin-bottom:2px">Build Your Reiki Business</h3><p>Learn and implement the key elements to starting and growing...</p></div>
</section>

<section class="testimonial">
  <h2 class="abs section-title">WHAT OUR <b>CLIENT SAY</b></h2>
  <div class="abs quote-badge">
    <svg width="78" height="78" viewBox="0 0 78 78" aria-hidden="true"><g fill="#fff"><circle cx="29" cy="41" r="9"/><path d="M22 41 Q22 26 36 22 L37 26 Q28 30 29 41Z"/><circle cx="49" cy="41" r="9"/><path d="M42 41 Q42 26 56 22 L57 26 Q48 30 49 41Z"/></g></svg>
  </div>
  <div class="abs arrow" style="left:77px;top:135px"><svg width="46" height="46" viewBox="0 0 46 46" aria-hidden="true"><path d="M26 15 L18 23 L26 31" fill="none" stroke="#fff" stroke-width="2.5"/></svg></div>
  <div class="abs arrow" style="left:1073px;top:135px"><svg width="46" height="46" viewBox="0 0 46 46" aria-hidden="true"><path d="M20 15 L28 23 L20 31" fill="none" stroke="#fff" stroke-width="2.5"/></svg></div>
  <p class="abs quote">" I was drawn to this course with the desire to heal family, friends and pets and this course has given me that ability and more. With it, Reiki has healed me on many levels and given me insight into my own spirituality and to what is possible. The continued contact with Dana Whitlow on the community group page as well as input and questions and answers from other "</p>
  <p class="abs author">—&nbsp; Morgan Ellis</p>
</section>

<section class="blog">
  <h2 class="abs section-title">LATEST <b>BLOG</b></h2>
  <article class="abs card" style="left:76px">
    <div class="ph card-img" style="position:relative;background:linear-gradient(135deg,#6e2a3e,#b35a6c 50%,#3d6a5a)" role="img" aria-label="Photo of a round crystal grid arrangement"></div>
    <h4>Using Your Reiki Box to<br>Manifest Goals</h4>
    <p>We have entered anew year &amp; with that inevitably comes the desire to start fresh and create change.</p>
    <div class="more">READ MORE... <svg width="14" height="10" viewBox="0 0 14 10" aria-hidden="true"><path d="M1 1 L5 5 L1 9 M7 1 L11 5 L7 9" fill="none" stroke="#2f3142" stroke-width="1.6"/></svg></div>
  </article>
  <article class="abs card" style="left:346px">
    <div class="ph card-img" style="position:relative;background:linear-gradient(180deg,#5f87b8,#c9a985 60%,#7c8a96)" role="img" aria-label="Photo of stacked stones on a beach at sunset"></div>
    <h4>Why Reiki Does Not<br>Prescribe Or Diagnose</h4>
    <p>We have entered anew year &amp; with that inevitably comes the desire to start fresh and create change.</p>
    <div class="more">READ MORE... <svg width="14" height="10" viewBox="0 0 14 10" aria-hidden="true"><path d="M1 1 L5 5 L1 9 M7 1 L11 5 L7 9" fill="none" stroke="#2f3142" stroke-width="1.6"/></svg></div>
  </article>
  <article class="abs card" style="left:616px">
    <div class="ph card-img" style="position:relative;background:linear-gradient(135deg,#f1c7a0,#c77b52)" role="img" aria-label="Photo of a relaxing back massage"></div>
    <h4>Using Your Reiki Box to<br>Manifest Goals</h4>
    <p>We have entered anew year &amp; with that inevitably comes the desire to start fresh and create change.</p>
    <div class="more">READ MORE... <svg width="14" height="10" viewBox="0 0 14 10" aria-hidden="true"><path d="M1 1 L5 5 L1 9 M7 1 L11 5 L7 9" fill="none" stroke="#2f3142" stroke-width="1.6"/></svg></div>
  </article>
  <article class="abs card" style="left:886px">
    <div class="ph card-img" style="position:relative;background:linear-gradient(135deg,#f4f1ee,#d8c7bb)" role="img" aria-label="Photo of a hands-on healing session in a bright room"></div>
    <h4>Why Reiki Does Not<br>Prescribe Or Diagnose</h4>
    <p>We have entered anew year &amp; with that inevitably comes the desire to start fresh and create change.</p>
    <div class="more">READ MORE... <svg width="14" height="10" viewBox="0 0 14 10" aria-hidden="true"><path d="M1 1 L5 5 L1 9 M7 1 L11 5 L7 9" fill="none" stroke="#2f3142" stroke-width="1.6"/></svg></div>
  </article>
</section>

<section class="optin">
  <div class="ph optin-figure" role="img" aria-label="Photo of a woman with arms raised in warm sunlight"></div>
  <h2 class="abs optin-title">STAY <b>INSPIRED</b></h2>
  <p class="abs optin-text">Receive information and articles each month to keep you feeling inspired. As a thank-you, you will also receive access to soothing music you can download for</p>
  <div class="abs field" style="left:625px;top:165px">First Name*</div>
  <div class="abs field" style="left:625px;top:214px">Last Name*</div>
  <div class="abs field" style="left:625px;top:260px">Email Id*</div>
  <span class="abs btn btn-purple">Yes-Count Me In</span>
</section>

<footer class="newsletter">
  <h2 class="abs section-title">NEWSLETTER</h2>
  <p class="abs news-text">Would you like to receive exclusive access to articles, white papers and our regular monthly newsletter?</p>
  <div class="abs news-input">Enter Your Email Id*</div>
  <span class="abs btn btn-blue">Subscribe</span>
  <span class="abs social" style="left:502px;top:408px"></span>
  <span class="abs social" style="left:576px;top:408px"></span>
  <span class="abs social" style="left:650px;top:408px"></span>
  <ul class="abs foot-nav">
    <li class="active">Home</li><li>About</li><li>Courses</li><li>Blog</li><li>Student areas</li><li>Contact</li>
  </ul>
  <p class="abs copyright">©BRIGHT FERN STUDIES - 2016 All rights reserved.</p>
</footer>

</body>
</html>
```